Business card design needed

I would like a one sided black business card with the information provided above. Refer to my website www.brightvolleyracquets.com.au for an example of colors I have used for my site, would like to keep this consistent for my business cards also, I will upload my logo below.

I am a new small business that provides tennis customers with racquet re stringing, tennis strings and accessories.

Industry/Entity Type

Small Business

Contact Information for Business Card

Bright Volley Tennis

Owen Whitby
Managing Director

brightvolleyracquets@mailbox.example
www.brightvolleyracquets.com.au
0491 726 305

Racquet Restringing/Tennis Strings/Accessories

Requirements
Must have
• Must have my logo and card must be black

```html
<!DOCTYPE html>
<html lang="en">
<head>
<meta charset="utf-8">
<title>Bright Volley Tennis – Business Card</title>
<link rel="stylesheet" href="https://fonts.googleapis.com/css2?family=Roboto:wght@300;400;500&display=swap">
<style>
  :root {
    --backdrop: #e8e3dc;
    --card-black: #000000;
    --lime: #c4dd34;
    --lime-text: #b9d531;
    --navy-blue: #2f5797;
    --soft-white: #f2f2f2;
    --ink: #111111;
  }
  * { box-sizing: border-box; margin: 0; padding: 0; }
  html, body {
    width: 1200px;
    height: 475px;
    overflow: hidden;
    background: var(--backdrop);
    font-family: "Roboto", Arial, sans-serif;
  }
  .canvas { position: relative; width: 1200px; height: 475px; }

  .card {
    position: absolute;
    width: 547px;
    height: 313px;
    background: var(--card-black);
    overflow: hidden;
  }
  .card--front { left: 18px; top: 80px; border-radius: 14px; }
  .card--back  { left: 607px; top: 86px; border-radius: 28px; }

  .brand {
    position: absolute;
    left: 0; right: 0;
    display: flex;
    align-items: center;
    justify-content: center;
    gap: 12px;
  }
  .brand__dot {
    width: 30px; height: 30px;
    border-radius: 50%;
    background: var(--lime);
  }
  .brand__name {
    font-weight: 500;
    font-size: 31px;
    letter-spacing: 1px;
    text-transform: uppercase;
    color: var(--lime);
    white-space: nowrap;
  }
  .card--front .brand { top: 72px; }
  .card--back .brand  { top: 118px; }

  .holder {
    position: absolute;
    left: 70px; top: 180px;
    color: var(--lime-text);
  }
  .holder__name {
    font-size: 17px;
    font-weight: 400;
    letter-spacing: 1px;
    text-transform: uppercase;
    line-height: 20px;
  }
  .holder__role { font-size: 14px; font-weight: 300; line-height: 20px; }

  .divider {
    position: absolute;
    left: 230px; top: 180px;
    width: 1px; height: 40px;
    background: var(--soft-white);
  }

  .contact {
    position: absolute;
    left: 248px; top: 180px;
    color: var(--soft-white);
    font-size: 13px;
    font-weight: 300;
    line-height: 20px;
    letter-spacing: 0.3px;
    white-space: nowrap;
  }

  .footer-band {
    position: absolute;
    left: 0; right: 0; top: 238px; bottom: 0;
    background: linear-gradient(180deg, var(--navy-blue) 0%, var(--lime) 45%, var(--lime) 100%);
  }

  .front-url {
    position: absolute;
    left: 28px; top: 280px;
    font-size: 14px;
    color: var(--ink);
  }

  .back-url {
    position: absolute;
    left: 0; right: 0; top: 250px;
    text-align: center;
    font-size: 13px;
    letter-spacing: 2px;
    color: var(--soft-white);
    font-weight: 300;
  }
</style>
</head>
<body>
<main class="canvas">

  <section class="card card--front" aria-label="Business card front">
    <div class="brand">
      <span class="brand__dot"></span>
      <span class="brand__name">Bright Volley Tennis</span>
    </div>

    <div class="holder">
      <p class="holder__name">Owen Whitby</p>
      <p class="holder__role">Managing Director</p>
    </div>
    <span class="divider"></span>
    <div class="contact">
      <p>P : 0491 726 305</p>
      <p>E : brightvolleyracquets@mailbox.example</p>
    </div>

    <div class="footer-band" role="img" aria-label="Decorative blue and lime wave band along the card's lower edge"></div>
    <p class="front-url">www.brightvolleyracquets.com.au</p>
  </section>

  <section class="card card--back" aria-label="Business card back">
    <div class="brand">
      <span class="brand__dot"></span>
      <span class="brand__name">Bright Volley Tennis</span>
    </div>
    <p class="back-url">www.brightvolleyracquets.com.au</p>
  </section>

</main>
</body>
</html>
```